The World Most Wanted Eyelahes

1. We need a web design for a new company based in California, USA
2. We are the manufacturer for 100% human hair eyelashes,
made in Indonesia.
3. We recently launched "Tapered Eyelashes" with human hair.
Currently, none of the people carried Tapered eyelash.
4. We would like to see designs that use the 4 different colors that match with my products as "Four Seasons" concepts.
5. We prefer to follow www.pelvo.com style, like professional website.
6. Focus on products as a manufacturer, therefore, all wholesaler and retailer copy and paste to their marketing tools.
7. Need bilingual English and Spanish.
8. Easy to link with social media.

Target Market(s)

United States and Central/South America.

Industry/Entity Type

Hair

Number of Pages Required

5+ page

Requirements
Must have
• 1. Details of Products with image.
• 2. Hottest/Newest Items "Tapered in 100% Human Hair"
• 3. Store Page
Nice to have
• 1. My competitors is Quorim Eyelash. http://www.quorimlashes.com/
• Please follow the concepts of it.
• 2. www.Pelvo.com: They have great products detail on the website.
• i would like to focus on "Tapered" for new styles of the eyelash.
• 3. I want to visitors can write down the "Reviews" in every single product.
• Please check the www.QTRCosmetics.com.
Should not have
• It's not salon/Shop for the beauty.
• No need an appointment.
• We are the manufacturer of the eyelash.

```html
<!DOCTYPE html>
<html lang="en">
<head>
<meta charset="utf-8">
<title>Lumara Eyelashes</title>
<link href="https://fonts.googleapis.com/css2?family=Montserrat:wght@400;500;600;700&family=Source+Sans+3:wght@300;400;600&family=Hind:wght@500;600;700&display=swap" rel="stylesheet">
<style>
:root{
  --gold:#a87d3e;
  --nav-top:#a47b45;
  --nav-bottom:#8a6433;
  --brown:#5b3b2f;
  --rose:#b6638f;
  --grey-band:#efefef;
  --text:#333;
  --radiant:#e2b83e;
  --blooming:#e8a1a9;
  --alluring:#b44a99;
  --glowing:#97b9d3;
}
*{margin:0;padding:0;box-sizing:border-box}
html,body{width:1200px;height:1126px;overflow:hidden}
body{position:relative;background:#fff;font-family:"Source Sans 3",sans-serif;color:var(--text)}
.abs{position:absolute}
.header-band{left:0;top:0;width:1200px;height:120px;background:linear-gradient(#fff,#f0f0f0);border-bottom:1px solid #e4e4e4}
.mid-band{left:0;top:357px;width:1200px;height:465px;background:var(--grey-band);border-top:1px solid #e4e4e4}
.brand{left:117px;top:24px;font-family:"Montserrat",sans-serif;font-weight:400;font-size:40px;letter-spacing:2px;color:var(--gold)}
.phone{left:787px;top:15px;font-family:"Montserrat",sans-serif;font-size:15px;font-weight:500;color:var(--gold);display:flex;align-items:center;gap:6px}
.lang{left:950px;top:17px;font-family:"Montserrat",sans-serif;font-size:11px;display:flex;gap:16px;color:#222}
.lang .active{color:var(--gold)}
.main-nav{left:99px;top:95px;width:1002px;height:51px;background:linear-gradient(var(--nav-top),var(--nav-bottom));display:flex;align-items:center;padding-left:28px}
.main-nav a{color:#fff;text-decoration:none;font-family:"Montserrat",sans-serif;font-weight:500;font-size:13.5px;margin-right:31px}
.search{position:absolute;left:841px;top:10px;width:149px;height:31px;background:#fff;border-radius:2px;display:flex;align-items:center;padding-left:10px;gap:10px;font-size:13.5px;color:#777}
.hero{left:99px;top:146px;width:1002px;height:422px;background:#fff;border:1px solid #e2e2e2;overflow:hidden}
.hero-photo{position:absolute;left:330px;top:0;width:672px;height:422px;background:linear-gradient(90deg,#fff 0%,#e9d2c4 22%,#d4ac92 55%,#b98d74 80%,#8f6b55 100%)}
.hero-products{position:absolute;left:34px;top:164px;width:412px;height:210px;border-radius:14px;background:linear-gradient(135deg,#f3c9d6,#d8a84a 45%,#b44a99 75%,#b9c6d8)}
.hero-kicker{position:absolute;left:56px;top:56px;font-family:"Montserrat",sans-serif;font-size:15px;color:var(--rose);letter-spacing:.5px}
.hero-title{position:absolute;left:55px;top:80px;font-family:"Montserrat",sans-serif;font-weight:700;font-size:33px;line-height:37px;color:var(--brown)}
.slide-btn{position:absolute;top:353px;width:38px;height:38px;border-radius:50%;background:rgba(70,70,70,.55);display:flex;align-items:center;justify-content:center}
.card{top:588px;width:234px;height:206px;color:#fff}
.card .badge{position:absolute;left:-17px;top:-17px;width:98px;height:98px;border-radius:50%;background:rgba(255,255,255,.35);border:3px solid rgba(255,255,255,.5)}
.card h3{position:absolute;right:10px;top:12px;text-align:right;font-family:"Hind",sans-serif;font-weight:600;font-size:21px;line-height:28px}
.card h3 small{font-size:15px}
.card h3 b{font-size:26px;font-weight:600}
.card p{position:absolute;left:14px;right:10px;top:92px;text-align:center;font-weight:300;font-size:12.4px;line-height:15.5px}
.radiant{left:99px;background:var(--radiant)}
.blooming{left:353px;background:var(--blooming)}
.alluring{left:608px;background:var(--alluring)}
.glowing{left:863px;background:var(--glowing)}
.footer h2{font-weight:400;font-size:28px;color:#333}
.quick-links{left:124px;top:848px}
.quick-links ul{margin-top:16px;list-style:none}
.quick-links li{font-size:15.5px;line-height:25.7px;padding-left:22px;position:relative}
.quick-links li::before{content:"";position:absolute;left:6px;top:10px;width:5px;height:5px;border-radius:50%;background:#333}
.contact{left:376px;top:848px}
.contact-item{position:absolute;left:0;display:flex;gap:10px;font-size:13.6px;line-height:20.6px;white-space:nowrap}
.contact-item svg{flex:none;margin-top:3px}
.map{left:577px;top:883px;width:223px;height:163px;background:linear-gradient(135deg,#efe6c4,#e4dcc0 50%,#d9e4c9);border:1px solid #ddd}
.follow{left:875px;top:850px}
.social{position:absolute;left:0;display:flex;align-items:center;gap:16px;font-size:14px;white-space:nowrap}
.social i{width:32px;height:32px;border-radius:5px;display:block}
.copyright{left:771px;top:1091px;font-size:12px}
</style>
</head>
<body>
<div class="abs header-band"></div>
<div class="abs mid-band"></div>

<div class="abs brand">LUMARA</div>
<div class="abs phone">
  <svg width="8" height="12" viewBox="0 0 8 12"><rect x="0.8" y="0.8" width="6.4" height="10.4" rx="1" fill="none" stroke="#a87d3e" stroke-width="1.5"/><circle cx="4" cy="9.3" r=".8" fill="#a87d3e"/></svg>
  1-800 555 0142
</div>
<div class="abs lang"><span class="active">ENGLISH</span><span>|</span><span>SPANISH</span></div>

<nav class="abs main-nav">
  <a href="#">Home</a><a href="#">About Us</a><a href="#">Products</a><a href="#">Blog</a><a href="#">Shop</a><a href="#">Testimonials</a><a href="#">Contact Us</a>
  <div class="search">
    <svg width="17" height="17" viewBox="0 0 17 17"><circle cx="7" cy="7" r="5.5" fill="none" stroke="#666" stroke-width="2"/><line x1="11" y1="11" x2="15.5" y2="15.5" stroke="#666" stroke-width="2.4" stroke-linecap="round"/></svg>
    Search
  </div>
</nav>

<section class="abs hero">
  <div class="hero-photo" role="img" aria-label="Close-up portrait of a model wearing long lashes"></div>
  <div class="hero-products" role="img" aria-label="Assorted eyelash product packages"></div>
  <div class="hero-kicker">LUMARA</div>
  <h1 class="hero-title">Tapered in 100%<br>Human Hair</h1>
  <div class="slide-btn" style="left:891px"><svg width="10" height="18" viewBox="0 0 10 18"><path d="M8 2L2 9l6 7" fill="none" stroke="#ddd" stroke-width="1.5"/></svg></div>
  <div class="slide-btn" style="left:945px"><svg width="10" height="18" viewBox="0 0 10 18"><path d="M2 2l6 7-6 7" fill="none" stroke="#ddd" stroke-width="1.5"/></svg></div>
</section>

<article class="abs card radiant">
  <div class="badge"></div>
  <h3>RADIANT<br><small>YOUR</small> <b>EYES</b></h3>
  <p>Lorem ipsum dolor sit amet, consectetur adipiscing. In metus diam, fermentum in orci sit amet, lobortis congue diam. Interdum et malesuada fames ac ante ipsum primis in faucibus.</p>
</article>
<article class="abs card blooming">
  <div class="badge"></div>
  <h3>BLOOMING<br><small>YOUR</small> <b>EYES</b></h3>
  <p>Lorem ipsum dolor sit amet, consectetur adipiscing. In metus diam, fermentum in orci sit amet, lobortis congue diam. Interdum et malesuada fames ac ante ipsum primis in faucibus.</p>
</article>
<article class="abs card alluring">
  <div class="badge"></div>
  <h3>ALLURING<br><small>YOUR</small> <b>EYES</b></h3>
  <p style="top:95px">Lorem ipsum dolor sit amet, consectetur adipiscing. In metus diam, fermentum in orci sit amet, lobortis congue diam. Interdum et malesuada fames ac ante ipsum primis in faucibus.</p>
</article>
<article class="abs card glowing">
  <div class="badge"></div>
  <h3>GLOWING<br><small>YOUR</small> <b>EYES</b></h3>
  <p style="top:95px">Lorem ipsum dolor sit amet, consectetur adipiscing. In metus diam, fermentum in orci sit amet, lobortis congue diam. Interdum et malesuada fames ac ante ipsum primis in faucibus.</p>
</article>

<footer class="footer">
  <div class="abs quick-links">
    <h2>Quick Links</h2>
    <ul><li>Home</li><li>About Us</li><li>Products</li><li>Blog</li><li>Shop</li><li>Testimonials</li><li>Contact Us</li></ul>
  </div>
  <div class="abs contact">
    <h2>Contact</h2>
    <div class="contact-item" style="top:46px;left:6px">
      <svg width="15" height="13" viewBox="0 0 15 13"><path d="M7.5 1L1 7h2v5h3.5V9h2v3H12V7h2z" fill="#333"/></svg>
      <span>Lorium Ipsum Deoi,<br>Suite 18, 2nd Level,<br>Lorem Ipsum is simply,<br>Sector-x, Northvale - 100200</span>
    </div>
    <div class="contact-item" style="top:150px;left:10px">
      <svg width="8" height="13" viewBox="0 0 8 13"><rect x="0.8" y="0.8" width="6.4" height="11.4" rx="1" fill="none" stroke="#333" stroke-width="1.5"/></svg>
      <span>Phone : 000-000-0000</span>
    </div>
    <div class="contact-item" style="top:191px;left:10px">
      <svg width="12" height="12" viewBox="0 0 12 12"><rect x="0" y="4" width="12" height="8" rx="1" fill="#333"/><rect x="2.5" y="0.5" width="7" height="4" fill="none" stroke="#333"/></svg>
      <span>Fax : 000 - 000 - 0000</span>
    </div>
  </div>
  <div class="abs map" role="img" aria-label="Street map showing office locations"></div>
  <div class="abs follow">
    <h2>Follow Us</h2>
    <div class="social" style="top:53px"><i style="background:#3e6eb5"></i>Socialbook</div>
    <div class="social" style="top:97px"><i style="background:#33b5cf"></i>Chirper</div>
    <div class="social" style="top:141px"><i style="background:#d8544a"></i>Circles Plus</div>
  </div>
  <div class="abs copyright">© 2015.www.companyname.com. All rights reserved.</div>
</footer>
</body>
</html>
```